Unique Business Card Design

Unique Business Card design for our orthotic and prosthetic company. Our logo is on our website, color is light blue. Unique shape (artificial leg shaped, vertical, etc..) preferred. Logo, business name, individual name and basic demographics needed.

Industry/Entity Type

Business

Contact Information for Business Card

Logo, Industry, Phone # Logo, "Prosthetic & Orthotic Services" Place to add individual name and contact info

Colors
cee9f5

Requirements
Must have
• The icon must be there, placement of "Prosthetic & Orthotic Services" can be moved
Nice to have
• Like the mix of light blue, and a little darker blue. One design included the icons from my website which was a nice touch

```html
<!DOCTYPE html>
<html lang="en">
<head>
<meta charset="utf-8">
<title>LimbWorks Inc. – Business Card</title>
<link rel="stylesheet" href="https://fonts.googleapis.com/css2?family=Open+Sans:wght@400;600;700&family=Libre+Baskerville:ital@1&display=swap">
<style>
  :root {
    --blue: #1f6ec4;
    --blue-deep: #185fae;
    --blue-light: #cee9f5;
    --white: #ffffff;
    --stage: #3a3a3a;
    --stage-edge: #141414;
    --sans: "Open Sans", Arial, sans-serif;
    --serif: "Libre Baskerville", Georgia, serif;
  }
  * { box-sizing: border-box; margin: 0; padding: 0; }
  html, body { width: 1200px; height: 950px; overflow: hidden; }
  body {
    background: radial-gradient(ellipse at 50% 45%, var(--stage) 0%, var(--stage-edge) 85%);
    font-family: var(--sans);
    position: relative;
  }
  .card {
    position: absolute;
    width: 700px;
    height: 400px;
    border-radius: 22px;
    overflow: hidden;
    box-shadow: 0 18px 40px rgba(0,0,0,.55);
  }

  /* Front */
  .card-front {
    left: 120px; top: 45px;
    background: linear-gradient(160deg, #2a7bd0 0%, var(--blue) 55%, var(--blue-deep) 100%);
    color: var(--white);
  }
  .front-mark {
    position: absolute; left: 80px; top: 130px;
    width: 130px; height: 130px; border-radius: 50%;
    background: var(--white);
  }
  .front-lockup { position: absolute; left: 240px; top: 138px; width: 400px; }
  .brand-name {
    font-family: var(--sans); font-weight: 700;
    font-size: 38px; letter-spacing: .5px; line-height: 1;
  }
  .front-lockup .rule { height: 3px; background: var(--white); margin: 8px 0 6px; width: 340px; }
  .tagline { font-family: var(--serif); font-style: italic; font-size: 17px; }
  .front-web {
    position: absolute; left: 0; right: 0; bottom: 55px;
    display: flex; align-items: center; justify-content: center; gap: 14px;
    font-size: 15px;
  }
  .front-web .line { width: 140px; height: 1px; background: rgba(255,255,255,.8); }

  /* Back */
  .card-back {
    left: 380px; top: 505px;
    background: var(--white);
  }
  .back-band {
    position: absolute; left: 0; right: 0; top: 222px; bottom: 0;
    background: var(--blue);
  }
  .back-lockup { position: absolute; left: 36px; top: 52px; display: flex; align-items: center; gap: 16px; }
  .back-mark { width: 90px; height: 90px; border-radius: 50%; background: var(--blue); flex: none; }
  .back-lockup .brand-name { color: var(--blue); font-size: 30px; }
  .back-lockup .rule { height: 2px; background: var(--blue); margin: 6px 0 5px; width: 270px; }
  .back-lockup .tagline { color: var(--blue); font-size: 14px; }
  .holder {
    position: absolute; left: 36px; top: 176px;
    color: var(--blue); font-weight: 700; font-size: 24px;
  }
  .holder .cred { font-weight: 400; font-size: 14px; margin-left: 4px; }
  .hero-mark {
    position: absolute; right: 36px; top: 128px;
    width: 170px; height: 170px; border-radius: 50%;
    background: var(--white); border: 6px solid var(--blue-light);
  }
  .contacts {
    position: absolute; left: 36px; top: 238px;
    list-style: none; color: var(--white); font-size: 15px;
  }
  .contacts li { display: flex; align-items: center; gap: 10px; height: 24px; }
  .contacts svg { width: 15px; height: 15px; flex: none; fill: var(--white); }
  .contacts .no-icon { padding-left: 25px; }
</style>
</head>
<body>

<section class="card card-front">
  <div class="front-mark"></div>
  <div class="front-lockup">
    <div class="brand-name">LIMBWORKS INC.</div>
    <div class="rule"></div>
    <div class="tagline">Prosthetic &amp; Orthotic Services</div>
  </div>
  <div class="front-web"><span class="line"></span><span>www.limbworksinc.com</span><span class="line"></span></div>
</section>

<section class="card card-back">
  <div class="back-band"></div>
  <div class="back-lockup">
    <div class="back-mark"></div>
    <div>
      <div class="brand-name">LIMBWORKS INC.</div>
      <div class="rule"></div>
      <div class="tagline">Prosthetic &amp; Orthotic Services</div>
    </div>
  </div>
  <div class="holder">Miriam Kessler,<span class="cred">CO LPO</span></div>
  <div class="hero-mark"></div>
  <ul class="contacts">
    <li><svg viewBox="0 0 16 16"><path d="M3 2h3l1.5 3.5-2 1.2a8 8 0 0 0 3.8 3.8l1.2-2L14 10v3a1 1 0 0 1-1 1A11 11 0 0 1 2 3a1 1 0 0 1 1-1z"/></svg>555.014.2200</li>
    <li><svg viewBox="0 0 16 16"><path d="M5 1h6a1 1 0 0 1 1 1v12a1 1 0 0 1-1 1H5a1 1 0 0 1-1-1V2a1 1 0 0 1 1-1zm0 2v9h6V3zm3 10a.8.8 0 1 0 0 1.6.8.8 0 0 0 0-1.6z"/></svg>555.014.2291</li>
    <li><svg viewBox="0 0 16 16"><path d="M4 1h7v4H4zM2 6h12a1 1 0 0 1 1 1v5h-3v3H4v-3H1V7a1 1 0 0 1 1-1zm3 5v3h6v-3z"/></svg>555-0147733</li>
    <li><svg viewBox="0 0 16 16"><path d="M1 3h14v10H1zm1.5 1.2V5l5.5 4 5.5-4v-.8z"/></svg>mkessler@limbworksinc.com</li>
    <li><svg viewBox="0 0 16 16"><path d="M8 1a7 7 0 1 0 0 14A7 7 0 0 0 8 1zm0 1.5c.8 0 1.8 1.8 2 4.5H6c.2-2.7 1.2-4.5 2-4.5zM2.6 7A5.5 5.5 0 0 1 5.4 3 9 9 0 0 0 4.5 7zm0 2h1.9a9 9 0 0 0 .9 4 5.5 5.5 0 0 1-2.8-4zM6 9h4c-.2 2.7-1.2 4.5-2 4.5S6.2 11.7 6 9zm5.5 0h1.9a5.5 5.5 0 0 1-2.8 4 9 9 0 0 0 .9-4zm0-2a9 9 0 0 0-.9-4 5.5 5.5 0 0 1 2.8 4z"/></svg>www.limbworksinc.com</li>
    <li class="no-icon">820 Harbor Ave., Riverton, NY 10999</li>
  </ul>
</section>

</body>
</html>
```